Awesome photographers card for an awesome new business

Double sided business card Black background and silver logo in middle on one side. Details on otherside. please keep it simple

Industry/Entity Type

Photographer

Contact Information for Business Card

Gerald Fenwick
0452817360
GeraldFenwickPhotography47@mailbox.test
www.GeraldFenwickPhotography.test.au
Instagram _Gerald_fenwick

Requirements
Must have
• My logo in Silver
• please use instagram logo instead of "Instagram"

```html
<!DOCTYPE html>
<html lang="en">
<head>
<meta charset="utf-8">
<title>Gerald Fenwick Photography – Business Card</title>
<link rel="stylesheet" href="https://fonts.googleapis.com/css2?family=Lato:wght@400;700&display=swap">
<style>
  :root {
    --backdrop: #1f1f1f;
    --card: #262626;
    --card-edge: #303030;
    --silver: #cfcfcf;
    --silver-soft: #a9a9a9;
    --rule: #4a4a4a;
    --ghost: #2f2f2f;
  }
  * { margin: 0; padding: 0; box-sizing: border-box; }
  html, body {
    width: 1200px; height: 880px; overflow: hidden;
    background: var(--backdrop);
    font-family: "Lato", Arial, sans-serif;
  }
  .stage { position: relative; width: 1200px; height: 880px; }
  .card {
    position: absolute;
    width: 560px; height: 320px;
    background: var(--card);
    border: 1px solid var(--card-edge);
    border-radius: 18px;
    overflow: hidden;
  }
  .card--front { left: 70px; top: 90px; }
  .card--back { left: 570px; top: 470px; }

  /* Front: brand mark */
  .brand {
    position: absolute; left: 50%; top: 50%;
    width: 180px; height: 180px;
    transform: translate(-50%, -50%);
    border: 3px solid var(--silver);
    border-radius: 50%;
    display: flex; flex-direction: column;
    align-items: center; justify-content: center;
    text-align: center;
    color: var(--silver);
    font-weight: 700;
    text-transform: uppercase;
    letter-spacing: 3px;
    font-size: 17px;
    line-height: 1.35;
  }
  .brand__line--small { font-size: 11px; letter-spacing: 4px; margin-top: 6px; }

  /* Back: contact details */
  .ghost-ring {
    position: absolute; left: 50%; top: 50%;
    width: 300px; height: 300px;
    transform: translate(-50%, -50%);
    border: 10px solid var(--ghost);
    border-radius: 50%;
  }
  .details {
    position: absolute; inset: 0;
    display: flex; flex-direction: column; align-items: center;
    padding-top: 34px;
    color: var(--silver);
    text-align: center;
  }
  .details__name {
    font-weight: 700; font-size: 19px;
    text-transform: uppercase; letter-spacing: 0.5px;
  }
  .rule { width: 300px; height: 1px; background: var(--rule); margin: 12px 0; }
  .contact { display: flex; flex-direction: column; align-items: center; gap: 4px; }
  .contact__item { display: flex; flex-direction: column; align-items: center; gap: 3px; font-size: 14px; color: var(--silver-soft); }
  .contact__item + .contact__item { margin-top: 4px; }
  .icon { width: 16px; height: 16px; }
  .details__web { font-size: 14px; color: var(--silver-soft); }
  .details__web strong { color: var(--silver); font-weight: 700; }
</style>
</head>
<body>
<main class="stage">
  <section class="card card--front" aria-label="Card front">
    <div class="brand">
      <span class="brand__line">Gerald</span>
      <span class="brand__line">Fenwick</span>
      <span class="brand__line brand__line--small">Photography</span>
    </div>
  </section>

  <section class="card card--back" aria-label="Card back">
    <div class="ghost-ring" aria-hidden="true"></div>
    <div class="details">
      <h1 class="details__name">Gerald Fenwick</h1>
      <div class="rule"></div>
      <div class="contact">
        <div class="contact__item">
          <svg class="icon" viewBox="0 0 16 16" aria-hidden="true">
            <circle cx="8" cy="8" r="7.3" fill="none" stroke="#bdbdbd" stroke-width="1.2"/>
            <path d="M5.3 4.6c.4-.3.9-.2 1.1.2l.6 1.2c.2.4.1.8-.2 1l-.4.3c.4.9 1.1 1.6 2 2l.3-.4c.3-.3.7-.4 1-.2l1.2.6c.4.2.5.7.2 1.1l-.5.6c-.4.4-1 .5-1.6.3-2-.8-3.5-2.3-4.3-4.3-.2-.6-.1-1.2.3-1.6z" fill="#bdbdbd"/>
          </svg>
          <span>0452817360</span>
        </div>
        <div class="contact__item">
          <svg class="icon" viewBox="0 0 16 16" aria-hidden="true">
            <circle cx="8" cy="8" r="7.3" fill="none" stroke="#bdbdbd" stroke-width="1.2"/>
            <rect x="4" y="5.2" width="8" height="5.6" rx="0.6" fill="none" stroke="#bdbdbd" stroke-width="1"/>
            <path d="M4.2 5.6 8 8.5l3.8-2.9" fill="none" stroke="#bdbdbd" stroke-width="1"/>
          </svg>
          <span>GeraldFenwickPhotography47@mailbox.test</span>
        </div>
        <div class="contact__item">
          <svg class="icon" viewBox="0 0 16 16" aria-hidden="true">
            <circle cx="8" cy="8" r="7.3" fill="none" stroke="#bdbdbd" stroke-width="1.2"/>
          </svg>
          <span>_Gerald_fenwick</span>
        </div>
      </div>
      <div class="rule"></div>
      <p class="details__web">www.<strong>GeraldFenwickPhotography</strong>.test.au</p>
    </div>
  </section>
</main>
</body>
</html>
```